Federal IT Consulting Company - Brisolux Consulting Group

We're seeking a skilled web designer to create a modern, bold, and engaging WordPress website for Brisolux Consulting Group, LLC. Our company specializes in federal IT consulting, and our name is a play on "Brightening Solutions." The website should reflect our expertise in the federal technology marketplace and position us as a trusted partner for clients navigating their IT journey.

contact: info@brisoluxgrp-example.com

Current Status

WordPress is already installed on our hosting account
We have an existing logo (may need modernization)

Design Requirements

Style:

Modern and visually striking design
Bold elements to convey confidence and expertise
Incorporate the concept of "brightening solutions" into the design

Features:

Modern UX sliders for dynamic content presentation
Eye-catching, high-quality images (stock photos to be sourced by the designer)
Responsive design for all devices

Color Scheme:

To be proposed by the designer, should align with our brand and convey trust and technological expertise

Logo:

Evaluate our current logo
Create a transparent background version if needed
Propose modernization if deemed necessary

Accessibility:

Ensure design elements are accessible to users with disabilities
Use high contrast ratios for text and background colors
Provide text alternatives for non-text content

Website Structure
Create the following pages, with the possibility of subpages:

Home
Services
About
Contact

Specific Page Requirements
Home Page

Striking hero section with a clear value proposition
Overview of our services
Client testimonials or trust indicators

Services Page

Detailed list of our IT consulting services
Clear explanation of how we help navigate the federal IT landscape

About Page

Company history and mission
Team highlights (if applicable)
Our approach to federal IT consulting

Contact Page

Contact form
Other contact methods (phone, email)

Technical Requirements

Fully responsive design
SEO best practices implemented
Fast loading times
Integration with necessary plugins (to be discussed)
Training on how to update and maintain the site
Full compliance with Web Content Accessibility Guidelines (WCAG) 2.1 Level AA
Adherence to Section 508 standards for federal website accessibility
Implementation of necessary features for ADA compliance
Updates

Designs look the same

Target Market(s)

US Federal Govt customers looking for IT support.

Industry/Entity Type

IT Consulting

Coding

Coded - Design and coding required

Colors
0054AA
0677BA
7BADD7
CADEEF
E8F1F8
0094D4
00A9DD
6FCCEA
C7EBF8
E9F6FB
00AB8E
00BBA5
67D7C9
C6EFE9
E9F9F6

```html
<!DOCTYPE html>
<html lang="en">
<head>
<meta charset="utf-8">
<title>Brisolux Consulting Group</title>
<link href="https://fonts.googleapis.com/css2?family=Michroma&family=Poppins:ital,wght@0,400;0,500;0,600;0,700;1,400;1,500&display=swap" rel="stylesheet">
<style>
:root{
  --blue:#0094D4;
  --blue-bright:#1e8fe0;
  --blue-deep:#0054AA;
  --navy:#0b2d4e;
  --navy-dark:#061c33;
  --ink:#111111;
  --text:#333333;
  --muted:#555555;
  --white:#ffffff;
  --display:"Michroma", sans-serif;
  --body:"Poppins", sans-serif;
}
*{margin:0;padding:0;box-sizing:border-box}
html,body{width:1200px;height:3766px;overflow:hidden}
body{position:relative;font-family:var(--body);color:var(--text);background:var(--white)}
a{color:inherit;text-decoration:none}

/* header */
.site-header{position:absolute;left:0;top:0;width:1200px;height:103px;background:var(--white);border-top:3px solid var(--blue)}
.brand{position:absolute;display:flex;align-items:center;gap:10px;font-family:var(--body);font-weight:700;letter-spacing:1px}
.brand-dot{width:34px;height:34px;border-radius:50%;background:var(--blue)}
.site-header .brand{left:66px;top:30px;font-size:30px;color:var(--ink)}
.main-nav{position:absolute;top:46px;font-size:14px;color:var(--ink)}
.main-nav span{position:absolute;white-space:nowrap}
.main-nav .active{color:var(--blue);font-weight:600}
.call{position:absolute;left:818px;top:28px;display:flex;align-items:center;gap:10px}
.call-icon{width:36px;height:36px;border-radius:50%;background:var(--ink);display:flex;align-items:center;justify-content:center}
.call small{display:block;font-size:12px;color:var(--ink)}
.call strong{display:block;font-size:19px;color:var(--navy);font-weight:600;line-height:1.1}
.btn{display:flex;align-items:center;justify-content:center;background:var(--blue-bright);color:var(--white);font-weight:600;font-size:13px;letter-spacing:.5px;border-radius:3px;box-shadow:0 4px 10px rgba(0,0,0,.18)}
.header-cta{position:absolute;left:1032px;top:30px;width:137px;height:43px}

/* hero */
.hero{position:absolute;left:0;top:103px;width:1200px;height:642px}
.hero-photo{position:absolute;inset:0;background:linear-gradient(100deg,#8a5a3a 0%,#c9a68c 28%,#9ea3a7 55%,#5b6670 80%,#2f3942 100%)}
.hero-strip{position:absolute;right:0;top:0;width:70px;height:642px;background:var(--navy-dark)}
.hero-title{position:absolute;right:120px;top:218px;text-align:right;color:var(--white);font-weight:600;font-size:35px;line-height:46px;text-shadow:0 2px 6px rgba(0,0,0,.35)}
.hero-title em{font-style:normal;color:var(--blue-bright)}
.hero-sub{position:absolute;right:120px;top:328px;color:var(--white);font-style:italic;font-size:17px}
.hero-cta{position:absolute;left:908px;top:375px;width:172px;height:42px}
.dots{position:absolute;display:flex;gap:14px}
.dots i{width:14px;height:14px;border:2px solid currentColor;border-radius:50%;display:block}
.dots i.on{background:var(--blue-bright);border-color:var(--blue-bright);box-shadow:0 0 0 2px var(--white)}
.hero .dots{left:981px;top:596px;color:var(--white)}
.social-rail{position:absolute;right:14px;top:194px;display:flex;flex-direction:column;align-items:center;gap:14px}
.ring{border:1.5px solid currentColor;border-radius:50%;display:block}
.scroll-label{writing-mode:vertical-rl;color:var(--white);font-size:12px;font-weight:600;letter-spacing:1px}

/* section titles */
.kicker{font-size:20px;color:var(--ink);letter-spacing:.5px}
.display{font-family:var(--display);color:var(--ink);letter-spacing:2px;line-height:1}

/* about */
.about-kicker{position:absolute;right:623px;top:890px}
.about-title{position:absolute;right:623px;top:928px;font-size:34px}
.about-text{position:absolute;left:120px;top:976px;width:458px;text-align:right;font-size:14.6px;line-height:25px;color:var(--text)}
.about-cta{position:absolute;left:450px;top:1175px;width:127px;height:43px}
.frame-tl{position:absolute;left:618px;top:837px;width:206px;height:300px;background:var(--blue-bright);clip-path:polygon(0 0,100% 0,96% 4%,4% 4%,4% 100%,0 100%)}
.frame-br{position:absolute;left:880px;top:1060px;width:206px;height:213px;background:var(--blue-bright);clip-path:polygon(100% 0,100% 100%,0 100%,3% 95%,95% 95%,95% 6%)}
.about-photo{position:absolute;left:630px;top:849px;width:443px;height:412px;background:linear-gradient(135deg,#b8b6ae,#8b8f94 45%,#caa98e 75%,#d6d2cb)}
.dot-pattern{position:absolute;left:1144px;top:837px;width:56px;height:195px;background:linear-gradient(180deg,#f6f7f8,#eef0f2)}

/* services */
.services{position:absolute;left:0;top:1360px;width:1200px;height:761px;background:radial-gradient(ellipse at 50% 90%,#15497a 0%,#0d3960 45%,#0a2f52 100%)}
.services .kicker,.services .display{color:var(--white)}
.svc-kicker{position:absolute;left:0;width:1200px;text-align:center;top:84px}
.svc-title{position:absolute;left:0;width:1200px;text-align:center;top:120px;font-size:38px}
.svc-card{position:absolute;top:229px;width:285px}
.svc-photo{height:247px;border:2px solid var(--blue-bright);border-radius:3px}
.svc-body{margin:0 12px;height:190px;background:var(--white);text-align:center;padding-top:52px;position:relative}
.svc-icon{position:absolute;left:50%;top:-28px;transform:translateX(-50%);width:58px;height:58px;background:var(--navy);border:2px solid var(--white);border-radius:4px;display:flex;align-items:center;justify-content:center}
.svc-body h3{font-size:20px;font-weight:600;color:var(--ink)}
.svc-body p{font-size:13px;line-height:18.5px;color:var(--text);padding:12px 12px 0}
.svc-body a{display:inline-block;margin-top:10px;font-size:14px;font-weight:500;color:var(--ink);border-bottom:1px solid var(--ink);line-height:18px}
.arrow-btn{position:absolute;top:425px;width:52px;height:52px;border-radius:50%;background:var(--white);display:flex;align-items:center;justify-content:center}

/* testimonials */
.testimonials{position:absolute;left:0;top:2121px;width:1200px;height:959px;background:linear-gradient(180deg,#eef0f2,#e6e8eb)}
.tst-kicker{position:absolute;left:0;width:1200px;text-align:center;top:82px}
.tst-title{position:absolute;left:0;width:1200px;text-align:center;top:120px;font-size:38px}
.quote{position:absolute;top:202px;width:449px;height:225px;background:var(--white);border-radius:10px;box-shadow:0 6px 18px rgba(0,0,0,.12);padding:36px 14px 0}
.quote::after{content:"";position:absolute;left:78px;bottom:-28px;width:36px;height:30px;background:var(--white);clip-path:polygon(0 0,100% 0,80% 100%)}
.quote h4{font-size:17px;font-weight:500;color:var(--blue-bright)}
.stars{position:absolute;right:18px;top:38px;display:flex;gap:4px}
.quote p{margin-top:8px;font-size:13.4px;line-height:20.5px;text-align:center;color:var(--text)}
.author{position:absolute;top:446px;display:flex;align-items:center;gap:14px}
.avatar{width:56px;height:56px;border-radius:50%;border:2px solid var(--navy);background:linear-gradient(180deg,#c7ccd2,#8c949d)}
.author strong{display:block;font-size:16px;font-weight:500;color:var(--ink)}
.author span{display:block;font-size:14px;color:var(--text)}
.testimonials .dots{left:556px;top:554px;color:var(--navy)}

/* contact */
.footer-bg{position:absolute;left:0;top:3080px;width:1200px;height:686px;background:#000}
.contact{position:absolute;left:107px;top:2789px;width:988px;height:628px;background:linear-gradient(160deg,#2a90da 0%,#1c7fce 50%,#1a74c2 100%);border-radius:4px}
.contact .kicker,.contact .display{color:var(--white)}
.ct-kicker{position:absolute;left:0;width:988px;text-align:center;top:66px}
.ct-title{position:absolute;left:0;width:988px;text-align:center;top:104px;font-size:38px}
.ct-sub{position:absolute;left:0;width:988px;text-align:center;top:152px;font-size:13px;color:var(--white);font-weight:500}
.field{position:absolute;left:144px;width:699px;height:43px;background:var(--white);display:flex;align-items:center;gap:14px;padding-left:14px;font-size:13px;color:var(--ink)}
.field.area{align-items:flex-start;padding-top:14px;height:124px}
.send{position:absolute;left:407px;top:526px;width:172px;height:44px;background:var(--navy);color:var(--white);display:flex;align-items:center;justify-content:center;font-weight:600;font-size:13px;letter-spacing:.5px}

/* footer */
.site-footer{position:absolute;left:0;top:3417px;width:1200px;height:349px;color:var(--white)}
.site-footer .brand{left:146px;top:92px;font-size:34px;color:var(--white)}
.foot-social{position:absolute;left:212px;top:182px;display:flex;gap:12px}
.foot-col{position:absolute;top:64px}
.foot-col h5{font-family:var(--display);font-weight:400;font-size:17px;letter-spacing:1px}
.foot-col hr{width:46px;border:0;border-top:2px solid var(--blue-bright);margin:9px 0 14px}
.foot-col li{list-style:none;font-size:13px;line-height:26px}
.foot-rule{position:absolute;left:111px;top:273px;width:978px;border-top:1px solid #444}
.foot-copy{position:absolute;left:117px;top:304px;font-size:12px}
.foot-legal{position:absolute;left:889px;top:304px;font-size:12px;word-spacing:2px}
</style>
</head>
<body>

<header class="site-header">
  <div class="brand"><span class="brand-dot"></span>BRISOLUX</div>
  <nav class="main-nav">
    <span class="active" style="left:450px">Home</span>
    <span style="left:522px">Services</span>
    <span style="left:612px">About Us</span>
    <span style="left:704px">Testimonials</span>
  </nav>
  <div class="call">
    <span class="call-icon"><svg width="16" height="16" viewBox="0 0 24 24"><path fill="#fff" d="M6.6 10.8a15 15 0 0 0 6.6 6.6l2.2-2.2a1 1 0 0 1 1-.25 11.4 11.4 0 0 0 3.6.57 1 1 0 0 1 1 1V20a1 1 0 0 1-1 1A17 17 0 0 1 3 4a1 1 0 0 1 1-1h3.5a1 1 0 0 1 1 1c0 1.25.2 2.45.57 3.57a1 1 0 0 1-.25 1z"/></svg></span>
    <div><small>Schedule A Call</small><strong>555-014-2090</strong></div>
  </div>
  <a class="btn header-cta" href="#contact">CONTACT US</a>
</header>

<section class="hero">
  <div class="hero-photo" role="img" aria-label="Two colleagues reviewing a tablet together in a bright office"></div>
  <h1 class="hero-title">Transform Your <em>Business</em> with<br>Expert IT Consulting</h1>
  <p class="hero-sub">Innovative Solutions for a Digital Future</p>
  <a class="btn hero-cta" href="#contact">GET STARTED TODAY</a>
  <div class="dots"><i></i><i></i><i class="on"></i><i></i></div>
  <div class="hero-strip"></div>
  <div class="social-rail">
    <span class="ring" style="width:34px;height:34px;color:var(--blue-bright)"></span>
    <span class="ring" style="width:12px;height:12px;color:#fff"></span>
    <span class="ring" style="width:12px;height:12px;color:#fff"></span>
    <span class="scroll-label">SCROLL DOWN</span>
    <svg width="12" height="60" viewBox="0 0 12 60"><path d="M6 0V58M1 52l5 6 5-6" fill="none" stroke="#fff" stroke-width="1.5"/></svg>
  </div>
</section>

<section class="about">
  <p class="kicker about-kicker">ABOUT</p>
  <h2 class="display about-title">BRISOLUX</h2>
  <p class="about-text">Karspiciatis unde omnis iste natus error sisaseet voluptatem accusantium doloremque laudantium, totam rem aperiam, eaque ipsa quae ab illo inventore veritatis eset qusaeseseasi architecto beatae vitae dicta sunt explicabo. Nemo esesnim ipsam voluptatem quia voluptas sit aspernatur asaut odseit aut fugit, sed quia consequuntur magni dolores eoses qsaui ratione voluptatem sequi nesciunt.</p>
  <a class="btn about-cta" href="#">LEARN MORE</a>
  <div class="frame-tl"></div>
  <div class="frame-br"></div>
  <div class="about-photo" role="img" aria-label="Consultant and client smiling at a laptop in a meeting"></div>
  <div class="dot-pattern" role="img" aria-label="Decorative dot pattern"></div>
</section>

<section class="services">
  <p class="kicker svc-kicker">WHAT WE DO</p>
  <h2 class="display svc-title">OUR SERVICES</h2>

  <article class="svc-card" style="left:114px">
    <div class="svc-photo" role="img" aria-label="Analyst at a wall of glowing security monitors" style="background:linear-gradient(160deg,#0e3b5e,#1d7fb8 50%,#0a2338)"></div>
    <div class="svc-body">
      <span class="svc-icon"><svg width="26" height="26" viewBox="0 0 24 24" fill="none" stroke="#fff" stroke-width="1.6"><path d="M12 2l8 3v6c0 5-3.5 9-8 11-4.5-2-8-6-8-11V5z"/><rect x="9" y="11" width="6" height="5" rx="1"/><path d="M10 11V9a2 2 0 0 1 4 0v2"/></svg></span>
      <h3>IT &amp; Cybersecurity</h3>
      <p>Perspiciatis unde omnis iste natus error sitvoluptatem. Kaspiciatis unde omnis iste natus.</p>
      <a href="#">Learn More</a>
    </div>
  </article>

  <article class="svc-card" style="left:457px">
    <div class="svc-photo" role="img" aria-label="Team meeting around a table in a glass office" style="background:linear-gradient(160deg,#dfe3e6,#9aa3ab 50%,#5d6872)"></div>
    <div class="svc-body">
      <span class="svc-icon"><svg width="26" height="26" viewBox="0 0 24 24" fill="none" stroke="#fff" stroke-width="1.6"><rect x="3" y="4" width="18" height="13" rx="1"/><circle cx="12" cy="10.5" r="3"/><path d="M8 21h8M12 17v4"/></svg></span>
      <h3>Project Consulting</h3>
      <p>Perspiciatis unde omnis iste natus error sitvoluptatem. Kaspiciatis unde omnis iste natus.</p>
      <a href="#">Learn More</a>
    </div>
  </article>

  <article class="svc-card" style="left:801px">
    <div class="svc-photo" role="img" aria-label="Parcel on a conveyor in a warehouse" style="background:linear-gradient(160deg,#5e7894,#b08a62 50%,#22374d)"></div>
    <div class="svc-body">
      <span class="svc-icon"><svg width="28" height="26" viewBox="0 0 26 24" fill="none" stroke="#fff" stroke-width="1.6"><rect x="2" y="6" width="14" height="11"/><path d="M16 10h5l3 4v3h-8"/><circle cx="7" cy="19" r="2"/><circle cx="19" cy="19" r="2"/></svg></span>
      <h3>Logistics &amp; Supply Chain</h3>
      <p>Perspiciatis unde omnis iste natus error sitvoluptatem. Kaspiciatis unde omnis iste natus.</p>
      <a href="#">Learn More</a>
    </div>
  </article>

  <span class="arrow-btn" style="left:30px" aria-label="Previous"><svg width="14" height="20" viewBox="0 0 14 20"><path d="M11 2L3 10l8 8" fill="none" stroke="#111" stroke-width="2.5"/></svg></span>
  <span class="arrow-btn" style="left:1114px" aria-label="Next"><svg width="14" height="20" viewBox="0 0 14 20"><path d="M3 2l8 8-8 8" fill="none" stroke="#111" stroke-width="2.5"/></svg></span>
</section>

<section class="testimonials">
  <p class="kicker tst-kicker">CLIENTS REVIEWS</p>
  <h2 class="display tst-title">CUSTOMER TESTIMONIALS</h2>

  <blockquote class="quote" style="left:120px">
    <h4>Amazing Experience!</h4>
    <div class="stars" aria-label="5 stars"><svg width="86" height="16" viewBox="0 0 86 16"><g fill="#f5a623"><path id="st" d="M8 0l2.4 5 5.4.6-4 3.7 1.1 5.4L8 12l-4.9 2.7 1.1-5.4-4-3.7L5.6 5z"/><use href="#st" x="17.5"/><use href="#st" x="35"/><use href="#st" x="52.5"/><use href="#st" x="70"/></g></svg></div>
    <p>“Karsp asesdiciatis unde omnis iste natus error sisaeset voluptatem accusantium doloremque laudantium, totam rem aperiam, eaque ipsases quae ab illo inventore veritatis eset qusaeseseasi architecto bascaes aseseatae vitae dicta sunt explicabo. Nemo esesnim ipsam voluptatem quia voluptas sit aspernatur asaut odseit aut fugitsed quia consequuntur.”</p>
  </blockquote>
  <div class="author" style="left:240px"><span class="avatar" role="img" aria-label="Reviewer portrait"></span><div><strong>Marek Holloway</strong><span>Orivane Labs, CEO</span></div></div>

  <blockquote class="quote" style="left:621px">
    <h4>Amazing Experience!</h4>
    <div class="stars" aria-label="5 stars"><svg width="86" height="16" viewBox="0 0 86 16"><g fill="#f5a623"><use href="#st"/><use href="#st" x="17.5"/><use href="#st" x="35"/><use href="#st" x="52.5"/><use href="#st" x="70"/></g></svg></div>
    <p>“Karsp asesdiciatis unde omnis iste natus error sisaeset voluptatem accusantium doloremque laudantium, totam rem aperiam, eaque ipsases quae ab illo inventore veritatis eset qusaeseseasi architecto bascaes aseseatae vitae dicta sunt explicabo. Nemo esesnim ipsam voluptatem quia voluptas sit aspernatur asaut odseit aut fugitsed quia consequuntur.”</p>
  </blockquote>
  <div class="author" style="left:741px"><span class="avatar" role="img" aria-label="Reviewer portrait"></span><div><strong>Marek Holloway</strong><span>Orivane Labs, CEO</span></div></div>

  <div class="dots"><i></i><i></i><i class="on"></i><i></i></div>
</section>

<div class="footer-bg"></div>

<section class="contact" id="contact">
  <p class="kicker ct-kicker">GET IN TOUCH</p>
  <h2 class="display ct-title">CONTACT US</h2>
  <p class="ct-sub">Perspiciatis unde omnis iste natus error sitvoluptatem.</p>
  <div class="field" style="top:188px"><svg width="14" height="14" viewBox="0 0 24 24" fill="#1e8fe0"><circle cx="12" cy="7" r="5"/><path d="M2 23c0-6 4.5-9 10-9s10 3 10 9z"/></svg>Your Name</div>
  <div class="field" style="top:248px"><svg width="16" height="12" viewBox="0 0 24 18" fill="none" stroke="#1e8fe0" stroke-width="2"><rect x="1" y="1" width="22" height="16"/><path d="M1 1l11 9 11-9"/></svg>Email</div>
  <div class="field" style="top:308px"><svg width="14" height="14" viewBox="0 0 24 24"><path fill="#1e8fe0" d="M6.6 10.8a15 15 0 0 0 6.6 6.6l2.2-2.2a1 1 0 0 1 1-.25 11.4 11.4 0 0 0 3.6.57 1 1 0 0 1 1 1V20a1 1 0 0 1-1 1A17 17 0 0 1 3 4a1 1 0 0 1 1-1h3.5a1 1 0 0 1 1 1c0 1.25.2 2.45.57 3.57a1 1 0 0 1-.25 1z"/></svg>Phone Number</div>
  <div class="field area" style="top:370px"><svg width="18" height="14" viewBox="0 0 26 20" fill="#1e8fe0"><path d="M0 0h16v11H6l-4 4v-4H0z"/><path d="M18 5h8v10h-2v4l-4-4h-8v-2h6z"/></svg>Write &nbsp;A Message</div>
  <a class="send" href="#">SEND MESSAGE</a>
</section>

<footer class="site-footer">
  <div class="brand"><span class="brand-dot" style="background:var(--white)"></span>BRISOLUX</div>
  <div class="foot-social">
    <span class="ring" style="width:26px;height:26px;color:#fff"></span>
    <span class="ring" style="width:26px;height:26px;color:#fff"></span>
    <span class="ring" style="width:26px;height:26px;color:#fff"></span>
  </div>
  <div class="foot-col" style="left:466px"><h5>Quick Links</h5><hr><ul><li>Home</li><li>Services</li><li>About Us</li><li>Testimonials</li><li>Contact Us</li></ul></div>
  <div class="foot-col" style="left:691px"><h5>Links</h5><hr><ul><li>Copyright</li><li>Legal</li><li>Privacy</li><li>Accessibility</li><li>Sitemap</li></ul></div>
  <div class="foot-col" style="left:880px"><h5>Support</h5><hr><ul><li>Team</li><li>About Us</li><li>Careers</li><li>Our Values</li><li>Contact Us</li></ul></div>
  <div class="foot-rule"></div>
  <p class="foot-copy">©2024. All rights reserved.</p>
  <p class="foot-legal">Privacy &nbsp;&nbsp;&nbsp;|&nbsp;&nbsp;&nbsp; Terms &amp; Conditions</p>
</footer>

</body>
</html>
```